BOLD & MINIMALIST DESIGN NEEDED

We want a very bold but minimalistic business card design that is impactful and utilizes both sides of the business card. Our current logo is included for your use.

We want bold fonts and good use of negative space. We don't want the logo to overpower the design.

Target Market(s)

Professionals who are building new commercial buildings.

Industry/Entity Type

Construction

Contact Information for Business Card

Name, Title, email, office phone, cell phone, website

Font styles to use
Serif
Sans Serif

Requirements
Must have
• Bold design!

```html
<!DOCTYPE html>
<html lang="en">
<head>
<meta charset="utf-8">
<title>Stonecrest Build – Business Card</title>
<link rel="stylesheet" href="https://fonts.googleapis.com/css2?family=Open+Sans:wght@400;700&display=swap">
<style>
  :root {
    --lime: #a2fd33;
    --forest: #136046;
    --icon-green: #1e5a34;
    --paper: #ffffff;
    --ink: #141414;
    --shadow: rgba(40, 70, 10, 0.55);
  }
  * { margin: 0; padding: 0; box-sizing: border-box; }
  html, body {
    width: 1200px;
    height: 536px;
    overflow: hidden;
    background: var(--lime);
    font-family: "Open Sans", Arial, sans-serif;
  }
  .stage { position: relative; width: 1200px; height: 536px; }

  .card {
    position: absolute;
    top: 126px;
    width: 508px;
    height: 290px;
    box-shadow: 10px 12px 16px var(--shadow);
  }

  /* Back side */
  .card-back { left: 57px; background: var(--forest); }
  .brand-tile {
    position: absolute;
    left: 168px;
    top: 62px;
    width: 171px;
    height: 171px;
    background: var(--paper);
    display: flex;
    align-items: center;
    justify-content: center;
  }
  .brand-name {
    font-weight: 700;
    color: var(--ink);
    letter-spacing: 0.04em;
    text-transform: uppercase;
    text-align: center;
    line-height: 1.15;
  }
  .brand-tile .brand-name { font-size: 18px; }

  /* Front side */
  .card-front { left: 607px; background: var(--paper); }
  .name-band {
    position: absolute;
    left: 0; top: 0;
    width: 145px;
    height: 100%;
    background: var(--forest);
    color: var(--paper);
  }
  .person-name, .person-title {
    position: absolute;
    writing-mode: vertical-rl;
    transform: rotate(180deg);
    white-space: nowrap;
    font-weight: 400;
  }
  .person-name { left: 42px; bottom: 36px; font-size: 44px; line-height: 1; }
  .person-title { left: 97px; bottom: 48px; font-size: 11px; line-height: 1; letter-spacing: 0.02em; }

  .card-front .brand-name {
    position: absolute;
    right: 36px;
    top: 176px;
    top: 48px;
    font-size: 13px;
  }

  .contact-list {
    position: absolute;
    left: 195px;
    top: 107px;
    list-style: none;
  }
  .contact-item {
    display: flex;
    align-items: center;
    height: 25px;
    margin-bottom: 11px;
    font-size: 13px;
    letter-spacing: 0.08em;
    color: var(--ink);
  }
  .contact-icon {
    width: 25px; height: 25px;
    flex: none;
    margin-right: 7px;
  }
</style>
</head>
<body>
<main class="stage">

  <section class="card card-back" aria-label="Card back">
    <div class="brand-tile">
      <span class="brand-name">Stonecrest<br>Build</span>
    </div>
  </section>

  <section class="card card-front" aria-label="Card front">
    <div class="name-band">
      <h1 class="person-name">Your Name</h1>
      <p class="person-title">Designation</p>
    </div>

    <span class="brand-name">Stonecrest<br>Build</span>

    <ul class="contact-list">
      <li class="contact-item">
        <svg class="contact-icon" viewBox="0 0 26 26" aria-hidden="true">
          <circle cx="13" cy="13" r="13" fill="var(--icon-green)"/>
          <g fill="none" stroke="#fff" stroke-width="1.3" stroke-linejoin="round">
            <rect x="6.5" y="9" width="13" height="9"/>
            <path d="M6.5 9 L13 14 L19.5 9"/>
            <path d="M6.5 18 L11 13.5 M19.5 18 L15 13.5"/>
          </g>
        </svg>
        yourmail@mailbox.com
      </li>
      <li class="contact-item">
        <svg class="contact-icon" viewBox="0 0 26 26" aria-hidden="true">
          <circle cx="13" cy="13" r="13" fill="var(--icon-green)"/>
          <g fill="none" stroke="#fff" stroke-width="1.3">
            <rect x="9" y="5.5" width="8" height="15" rx="1.3"/>
            <path d="M9 8h8M9 17.5h8"/>
          </g>
        </svg>
        +000 0000 00000
      </li>
      <li class="contact-item">
        <svg class="contact-icon" viewBox="0 0 26 26" aria-hidden="true">
          <circle cx="13" cy="13" r="13" fill="var(--icon-green)"/>
          <g fill="none" stroke="#fff" stroke-width="1.3" stroke-linecap="round">
            <path d="M8 7.5c-1.5 1-1.6 3 0 5.6 1.8 3 4 5 6.6 5.8 1.5.4 2.6-.2 3.2-1.2l-2.4-2.2-1.6 1c-1.5-.7-3-2.3-3.7-3.8l1-1.6L9 7.5z"/>
            <path d="M14.5 8.5a3.5 3.5 0 0 1 3 3M15 6a6 6 0 0 1 5 5"/>
          </g>
        </svg>
        +999 9999 99999
      </li>
      <li class="contact-item">
        <svg class="contact-icon" viewBox="0 0 26 26" aria-hidden="true">
          <circle cx="13" cy="13" r="13" fill="var(--icon-green)"/>
          <g fill="none" stroke="#fff" stroke-width="1.2">
            <circle cx="13" cy="13" r="7"/>
            <ellipse cx="13" cy="13" rx="3" ry="7"/>
            <path d="M6 13h14M7 9.5h12M7 16.5h12"/>
          </g>
        </svg>
        www.companyname.com
      </li>
    </ul>
  </section>

</main>
</body>
</html>
```